Harbourline Electrical Solutions

On one side. LOGO (underneath:) Commercial Industrial Residential

- NAME & CONTACT DETAILS

Marcus T. Hollings
Project Manager

(Cell icon) (441) 555-0187
(Email icon) hlelectricalsolutions@mailvento.com
(Facebook & Instagram icons )@hlelectricalsolutions

Other side: LOGO - underneath ELECTRICAL CONSTRUCTION & MAINTENANCE . LED LIGHTING & AUTOMATION . LIFE SAFETY SYSTEMS (FIRE ALARM / SECURITY) . DATA & COMMUNICATION

```html
<!DOCTYPE html>
<html lang="en">
<head>
<meta charset="utf-8">
<title>Harbourline Electrical Solutions – Business Card</title>
<link rel="stylesheet" href="https://fonts.googleapis.com/css2?family=Lato:wght@400;700&display=swap">
<style>
  :root {
    --backdrop: #1c1c1e;
    --teal: #145a6e;
    --slate: #4a4a4c;
    --paper: #ffffff;
    --ink: #4a4a4c;
    --rule: #c9c9c9;
    --light: #ffffff;
  }
  * { box-sizing: border-box; margin: 0; padding: 0; }
  html, body { width: 1200px; height: 900px; overflow: hidden; }
  body {
    background: var(--backdrop);
    font-family: "Lato", Arial, sans-serif;
    display: flex;
    flex-direction: column;
    align-items: center;
    justify-content: center;
    gap: 48px;
  }
  .card {
    width: 640px;
    height: 366px;
    border-radius: 3px;
    overflow: hidden;
    box-shadow: 0 12px 30px rgba(0,0,0,.55);
  }

  /* Services side */
  .card--services { display: flex; flex-direction: column; }
  .services__brand {
    background: var(--teal);
    height: 54%;
    display: flex;
    flex-direction: column;
    align-items: center;
    justify-content: center;
    gap: 14px;
    color: var(--light);
  }
  .brand-name {
    font-weight: 700;
    font-size: 30px;
    letter-spacing: 2px;
    text-transform: uppercase;
  }
  .brand-sectors {
    font-size: 15px;
    letter-spacing: 1px;
    text-transform: uppercase;
  }
  .services__list {
    background: var(--slate);
    flex: 1;
    list-style: none;
    display: flex;
    flex-direction: column;
    align-items: center;
    justify-content: center;
    gap: 4px;
    color: var(--light);
    font-size: 15px;
    letter-spacing: .6px;
    text-transform: uppercase;
  }

  /* Contact side */
  .card--contact {
    background: var(--paper);
    display: flex;
    align-items: center;
    padding: 0 40px 0 44px;
  }
  .contact__brand {
    width: 200px;
    color: var(--teal);
    font-weight: 700;
    font-size: 26px;
    letter-spacing: 1px;
    text-transform: uppercase;
    padding-top: 70px;
  }
  .contact__rule {
    width: 1px;
    height: 190px;
    background: var(--rule);
    margin: 0 24px 0 20px;
  }
  .contact__details { color: var(--ink); }
  .person-name {
    color: var(--teal);
    font-weight: 700;
    font-size: 21px;
    letter-spacing: .5px;
    text-transform: uppercase;
  }
  .person-role { font-size: 15px; margin-bottom: 12px; }
  .contact-list { list-style: none; display: flex; flex-direction: column; gap: 6px; }
  .contact-item { display: flex; align-items: center; gap: 8px; font-size: 15px; }
  .contact-icon { width: 22px; height: 22px; flex: none; }
</style>
</head>
<body>

  <section class="card card--services">
    <div class="services__brand">
      <p class="brand-name">Harbourline Electrical Solutions</p>
      <p class="brand-sectors">Commercial Industrial Residential</p>
    </div>
    <ul class="services__list">
      <li>Electrical Construction &amp; Maintenance</li>
      <li>LED Lighting &amp; Automation</li>
      <li>Data &amp; Communication</li>
      <li>Life Safety Systems (Fire Alarm / Security)</li>
    </ul>
  </section>

  <section class="card card--contact">
    <p class="contact__brand">Harbourline</p>
    <div class="contact__rule"></div>
    <div class="contact__details">
      <p class="person-name">Marcus T. Hollings</p>
      <p class="person-role">Project Manager</p>
      <ul class="contact-list">
        <li class="contact-item">
          <svg class="contact-icon" viewBox="0 0 22 22" aria-hidden="true">
            <circle cx="11" cy="11" r="10" fill="none" stroke="#145a6e" stroke-width="1.3"/>
            <rect x="7.5" y="5" width="7" height="12" rx="1.2" fill="none" stroke="#145a6e" stroke-width="1.3"/>
            <line x1="10" y1="15" x2="12" y2="15" stroke="#145a6e" stroke-width="1.2"/>
          </svg>
          <span>(441) 555-0187</span>
        </li>
        <li class="contact-item">
          <svg class="contact-icon" viewBox="0 0 22 22" aria-hidden="true">
            <circle cx="11" cy="11" r="10" fill="none" stroke="#145a6e" stroke-width="1.3"/>
            <rect x="5.5" y="7" width="11" height="8" fill="#145a6e"/>
            <polyline points="5.5,7 11,11.5 16.5,7" fill="none" stroke="#ffffff" stroke-width="1.2"/>
          </svg>
          <span>hlelectricalsolutions@mailvento.com</span>
        </li>
        <li class="contact-item">
          <svg class="contact-icon" viewBox="0 0 22 22" aria-hidden="true">
            <circle cx="11" cy="11" r="10" fill="none" stroke="#145a6e" stroke-width="1.3"/>
          </svg>
          <span>@hlelectricalsolutions</span>
        </li>
        <li class="contact-item">
          <svg class="contact-icon" viewBox="0 0 22 22" aria-hidden="true">
            <circle cx="11" cy="11" r="10" fill="none" stroke="#145a6e" stroke-width="1.3"/>
          </svg>
          <span>@hlelectricalsolutions</span>
        </li>
      </ul>
    </div>
  </section>

</body>
</html>
```